Advanced Therapeutic Massage Therapist

I need a business card advertising my massage services as an advanced therapeutic massage therapist. I offer advanced therapeutic massage, swedish and deep tissue. I want to create a simple, professional and feminine card. I like bright colours and creativity.

I prefer a bold and experimental approach rather than something status-quo. A card to suggest therapeutic healing through dynamic massage. Motifs, shapes or layout which suggest movement and flow.
Updates

Target Market(s)

Everybody!

Industry/Entity Type

Health And Wellness

Contact Information for Business Card

The card should include:
My name, logo, services offered and my contact details.

Sláine Dunleavy
Massage Therapist

- Swedish - Deep Tissue - Advanced Therapeutic

Phone: (+353) 87 216 4093
Email: regenerate@slainedunleavy-example.com
Website: www.slainedunlevy-example.com

Font styles to use
Serif
Sans Serif
Decorative
Script

Colors

Designer to choose colors to be used in the design.

Requirements
Must have
• An example may contain something like this, yet concise:
• "Sláine Dunleavy
• Massage Therapist
• - Swedish - Deep Tissue - Advanced Therapeutic"
Nice to have
• This sentence is optional:
• Imagery such as a logo or symbol. I have attached a file containing a logo I had produced however the name is incorrect now as it is "Sláine" not "Nelly". It could be edited to change it to Sláine.
• I have sent the file as .psd .jpg. .pdf and .png
• I like when the card conveys energy, movement, pressure points, flow etc.
• I just like the designer to follow their own style and ideas. I like bright colours but must have a lot of a base colour to offset it. I really prefer them to follow their own inspiration. That is my preference.
Should not have
• Pine trees, non-native trees to Britain and Ireland, exotic flowers or animals that are not native to Britain and Ireland.
• I don't like brown as the background colour of the card.
• The cars shouldn't look like a wedding invitation i.e too many floral type designs.

```html
<!DOCTYPE html>
<html lang="en">
<head>
<meta charset="utf-8">
<title>Sláine Dunleavy – Massage Therapist Business Card</title>
<link href="https://fonts.googleapis.com/css2?family=Great+Vibes&family=Didact+Gothic&display=swap" rel="stylesheet">
<style>
  :root {
    --stage: #676767;
    --card-white: #fafafa;
    --mint-light: #bfe8dc;
    --mint: #9fdccb;
    --mint-deep: #86cfbb;
    --gold: #c9a24a;
    --gold-light: #e6c97a;
    --ink: #2b2b2b;
    --ink-soft: #444;
  }
  * { margin: 0; padding: 0; box-sizing: border-box; }
  html, body { width: 1200px; height: 550px; overflow: hidden; }
  body {
    background: var(--stage);
    font-family: "Didact Gothic", "Century Gothic", sans-serif;
    color: var(--ink);
    position: relative;
  }
  .card {
    position: absolute;
    top: 157px;
    width: 391px;
    height: 236px;
    overflow: hidden;
  }
  .card--front {
    left: 195px;
    background:
      radial-gradient(ellipse at 20% 15%, rgba(255,255,255,.35), transparent 55%),
      radial-gradient(ellipse at 80% 70%, rgba(120,200,180,.35), transparent 60%),
      radial-gradient(ellipse at 15% 85%, rgba(110,190,175,.3), transparent 50%),
      linear-gradient(160deg, var(--mint-light), var(--mint));
  }
  .card--back {
    left: 614px;
    background: var(--card-white);
  }
  .brand-mark {
    position: absolute;
    border-radius: 50%;
    border: 2px solid var(--gold);
    background: radial-gradient(circle at 50% 45%, var(--mint-light), var(--mint-deep));
    display: flex;
    align-items: center;
    justify-content: center;
    text-align: center;
  }
  .brand-mark__name {
    font-family: "Didact Gothic", "Century Gothic", sans-serif;
    color: var(--gold);
    font-size: 13px;
    line-height: 1.2;
    letter-spacing: .5px;
  }
  .card--front .brand-mark { left: 139px; top: 45px; width: 112px; height: 112px; }
  .card--back .brand-mark { left: 40px; top: 58px; width: 110px; height: 110px; }

  .signature {
    font-family: "Great Vibes", cursive;
    color: var(--ink);
    font-weight: 400;
    line-height: 1;
    white-space: nowrap;
  }
  .role {
    font-size: 10px;
    letter-spacing: 1.2px;
    color: var(--ink-soft);
    line-height: 1;
    white-space: nowrap;
  }
  .front-title {
    position: absolute;
    left: 0; right: 0; top: 160px;
    text-align: center;
  }
  .front-title .signature { font-size: 24px; }

  .divider {
    position: absolute;
    left: 173px; top: 53px;
    width: 2px; height: 117px;
    background: linear-gradient(var(--gold-light), var(--gold));
  }
  .back-title { position: absolute; left: 195px; top: 58px; }
  .back-title .signature { font-size: 24px; }
  .back-title .role { margin: 1px 0 0 7px; }

  .contact-list {
    position: absolute;
    left: 198px; top: 112px;
    list-style: none;
  }
  .contact-list li {
    display: flex;
    align-items: center;
    height: 17px;
    font-size: 9.5px;
    white-space: nowrap;
    color: var(--ink);
  }
  .contact-list svg { flex: none; width: 9px; height: 9px; margin-right: 7px; fill: var(--ink); }

  .services-band {
    position: absolute;
    left: 0; bottom: 0;
    width: 100%; height: 23px;
    background: linear-gradient(90deg, var(--mint), var(--mint-light) 40%, var(--mint) 75%, var(--mint-deep));
    display: flex; align-items: center; justify-content: center;
    font-size: 11px;
    white-space: nowrap;
    color: var(--ink);
  }
</style>
</head>
<body>
  <section class="card card--front">
    <div class="brand-mark" role="img" aria-label="Brand mark: gold ring around a mint disc">
      <span class="brand-mark__name">Sláine<br>Dunleavy</span>
    </div>
    <div class="front-title">
      <div class="signature">Sláine Dunleavy</div>
      <div class="role">massage therapist</div>
    </div>
  </section>

  <section class="card card--back">
    <div class="brand-mark" role="img" aria-label="Brand mark: gold ring around a mint disc">
      <span class="brand-mark__name">Sláine<br>Dunleavy</span>
    </div>
    <div class="divider"></div>
    <div class="back-title">
      <div class="signature">Sláine Dunleavy</div>
      <div class="role">massage therapist</div>
    </div>
    <ul class="contact-list">
      <li>
        <svg viewBox="0 0 10 10" aria-hidden="true"><path d="M1 3 Q1 1 5 1 Q9 1 9 3 L7 3.8 L6.5 2.8 L3.5 2.8 L3 3.8 Z M2.5 4.5 L7.5 4.5 L9 9 L1 9 Z"/></svg>
        (+353) 87 216 4093
      </li>
      <li>
        <svg viewBox="0 0 10 10" aria-hidden="true"><path d="M0.5 2 H9.5 V8 H0.5 Z M1.2 2.6 L5 5.6 L8.8 2.6" stroke="#fafafa" stroke-width=".7"/></svg>
        slaine@slainedunleavy-example.com
      </li>
      <li>
        <svg viewBox="0 0 10 10" aria-hidden="true"><circle cx="5" cy="5" r="4.5"/><path d="M0.5 5 H9.5 M5 0.5 V9.5 M5 .5 Q2 5 5 9.5 M5 .5 Q8 5 5 9.5 M1.3 2.8 H8.7 M1.3 7.2 H8.7" stroke="#fafafa" stroke-width=".6" fill="none"/></svg>
        www.slainedunlevy-example.com
      </li>
    </ul>
    <div class="services-band">Swedish - Deep Tissue - Advanced Therapeutic</div>
  </section>
</body>
</html>
```